WordPress webdesign with coding for our company BRISK The Answer

BRISK The Answer is a payrolling company such as Montaval Wages (one of our competitor https://www.montaval-wages.ch/fr/). We need to set up our website in both languages (Fr and Eng). Our logo is enclosed.
we would like something simple explaining what is payrolling in Graph and wording, who we are and a contact page. you can also take some example if needed from our mother company BRISK The Horizon (www.briskthehorizon.ch) or our sister company (www.briskyourstride.ch). we would like to keep the color panel of our logo (ref. Black = PANTONE P Process Black C
Pink = PANTONE P Process Magenta C
Grey = PANTONE 430 C) as the driver of the website.

```html
<!DOCTYPE html>
<html lang="en">
<head>
<meta charset="utf-8">
<title>BRISK The Answer – Payrolling</title>
<link href="https://fonts.googleapis.com/css2?family=Poppins:wght@300;400;500;600;700&display=swap" rel="stylesheet">
<style>
:root{
  --pink:#e5177e;
  --pink-soft:#fbe3ef;
  --black:#1e1c1d;
  --ink:#222;
  --grey:#6b6e70;
  --grey-dark:#424242;
  --grey-bg:#eceef0;
  --light:#f3f3f3;
  --white:#fff;
}
*{box-sizing:border-box;margin:0;padding:0}
html,body{width:1200px;height:4640px;overflow:hidden}
body{font-family:'Poppins',sans-serif;color:var(--ink);background:var(--white);position:relative}
section,header,footer{position:absolute;left:0;width:1200px;overflow:hidden}
.abs{position:absolute}
.btn{position:absolute;display:flex;align-items:center;justify-content:center;border-radius:22px;font-size:13px;font-weight:600;color:var(--white);background:var(--pink);text-transform:uppercase;letter-spacing:.2px}
.tick{position:absolute;left:50%;transform:translateX(-50%)}
.h2{position:absolute;left:0;width:100%;text-align:center;font-weight:600;font-size:35px;text-transform:uppercase;letter-spacing:.5px}
.logo{font-weight:700;white-space:nowrap}

/* hero */
.hero{top:0;height:665px;background:linear-gradient(180deg,#fff 0%,#fff 55%,var(--pink-soft) 100%)}
.nav{position:absolute;top:0;left:88px;width:1004px;height:96px;border-bottom:1px solid #d8d8d8}
.nav .logo{position:absolute;left:54px;top:32px;font-size:21px;color:var(--black)}
.nav ul{position:absolute;left:310px;top:38px;display:flex;gap:30px;list-style:none;font-size:14px;color:#333}
.nav ul li.active{color:var(--pink);font-weight:600}
.nav .tools{position:absolute;right:36px;top:34px;display:flex;gap:26px;align-items:center;font-size:13px}
.hero h1{position:absolute;left:142px;top:202px;font-size:40px;line-height:53px;font-weight:600;color:var(--black)}
.hero .lead{position:absolute;left:144px;top:328px;width:430px;font-size:18px;line-height:30px;color:var(--grey)}
.clients{position:absolute;left:150px;top:508px;display:flex;align-items:center}
.clients span{width:44px;height:44px;border-radius:50%;border:2px solid #fff;margin-right:-12px;background:linear-gradient(135deg,#a5745a,#5a3c30)}
.clients div{margin-left:34px}
.clients b{display:block;font-size:20px;font-weight:600}
.clients small{font-size:14px;color:#333}
.card{position:absolute;background:#fff;border-radius:8px;box-shadow:0 6px 24px rgba(0,0,0,.12);font-size:7px;color:#555}

/* services */
.services{top:665px;height:601px;background:var(--black)}
.services .h2{top:107px;color:#fff}
.svc{position:absolute;width:300px;text-align:center;color:#fff}
.svc .ring{display:block;margin:0 auto}
.svc h3{font-size:17px;font-weight:500;margin-top:20px}
.svc p{font-size:13px;line-height:25px;margin-top:10px;color:#e6e6e6}

/* partner */
.partner{top:1266px;height:694px;background:radial-gradient(circle at 0 10%,#fbd3e6 0,#fff 30%)}
.partner .h2{line-height:52px;top:116px}
.partner .h2 span{color:#555}
.features{position:absolute;left:95px;top:294px;width:1012px;height:246px;background:#fff;box-shadow:0 8px 30px rgba(0,0,0,.05)}
.feat{position:absolute;top:0;height:246px;width:253px;border-right:1px solid #eee;padding:70px 20px 0 24px}
.feat .dia{position:absolute;left:50%;top:-34px;width:62px;height:62px;margin-left:-31px;transform:rotate(45deg);background:var(--grey-dark)}
.feat .dia.pink{background:var(--pink)}
.feat h4{font-size:13px;font-weight:600;line-height:21px;text-transform:uppercase;min-height:42px}
.feat ul{list-style:none;margin-top:12px;font-size:12px;line-height:21px;color:#444}
.feat li{position:relative;padding-left:16px;margin-bottom:20px}
.feat li::before{content:"";position:absolute;left:0;top:6px;width:7px;height:4px;border-left:1.5px solid var(--pink);border-bottom:1.5px solid var(--pink);transform:rotate(-45deg)}

/* solution */
.solution{top:1960px;height:648px;background:var(--grey-bg)}
.solution h2{position:absolute;left:142px;top:145px;font-size:35px;font-weight:600;text-transform:uppercase}
.solution h2 span{font-weight:400;color:#444}
.solution p{position:absolute;left:143px;width:420px;font-size:12px;line-height:26px;color:#555}
.photo-right{position:absolute;right:0;top:0;width:520px;height:648px;background:linear-gradient(120deg,#dfe3e6,#c9d0d4 55%,#eef0f1)}

/* why */
.why{top:2608px;height:607px;background:linear-gradient(180deg,#fff 0%,#fff 65%,var(--pink-soft) 100%)}
.why .h2{top:130px}
.bubble{position:absolute;width:262px;height:262px;border-radius:50%;background:var(--grey-dark);color:#fff;text-align:center;padding-top:120px}
.bubble.pink{background:var(--pink)}
.bubble h5{font-size:14px;font-weight:600;text-transform:uppercase}
.bubble i{display:block;width:30px;height:2px;background:rgba(255,255,255,.6);margin:8px auto 14px}
.bubble p{font-size:12px;line-height:23px;width:170px;margin:0 auto}
.bubble svg{position:absolute;left:50%;top:46px;transform:translateX(-50%)}

/* testimonials */
.testimonials{top:3215px;height:553px;background:var(--light)}
.testimonials .h2{top:130px}
.testimonials .h2 span{font-weight:400;color:#444}
.avatar{position:absolute;left:564px;top:208px;width:74px;height:74px;border-radius:50%;background:linear-gradient(135deg,#d9a27e,#6b4a39)}
.quote{position:absolute;left:290px;top:296px;width:620px;text-align:center;font-size:13px;line-height:26px;color:#666}
.who{position:absolute;left:0;width:100%;top:440px;text-align:center;font-size:13px}
.who b{display:block;font-weight:500}
.who span{color:var(--pink);font-weight:500;line-height:26px}
.arrow{position:absolute;top:288px;width:58px;height:58px;border-radius:50%;background:#fff;box-shadow:0 4px 16px rgba(0,0,0,.08);display:flex;align-items:center;justify-content:center}

/* cta */
.cta{top:3768px;height:457px;background:var(--pink);color:#fff;text-align:center}
.cta h2{position:absolute;left:0;width:100%;top:96px;font-size:35px;font-weight:600;line-height:52px;text-transform:uppercase}
.cta p{position:absolute;left:240px;width:720px;top:236px;font-size:16px;line-height:28px}
.cta .btn{left:467px;top:318px;width:266px;height:42px;background:var(--black);text-transform:none;font-size:13px}

/* footer */
footer{top:4225px;height:415px;background:var(--black);color:#fff}
footer .logo{position:absolute;left:148px;top:116px;font-size:21px;color:#fff}
.social{position:absolute;left:146px;top:186px;display:flex;gap:10px}
.social span{width:36px;height:36px;border-radius:50%;background:#fff}
.col{position:absolute;top:98px;font-size:13px;line-height:25px}
.col h6{font-size:14px;font-weight:500;color:var(--pink);margin-bottom:6px}
.legal{position:absolute;left:0;top:270px;width:100%;height:145px;border-top:1px solid #3a3a3a;text-align:center;font-size:12px;padding-top:48px}
</style>
</head>
<body>

<header class="hero">
  <div class="nav">
    <div class="logo">BRISK The Answer</div>
    <ul>
      <li class="active">Home</li><li>About Us</li><li>What Is Payrolling?</li><li>Agency</li><li>Blog</li><li>Contact</li>
    </ul>
    <div class="tools">
      <svg width="16" height="16" viewBox="0 0 16 16" fill="none" stroke="#222" stroke-width="1.5"><circle cx="8" cy="5" r="3"/><path d="M2 15c0-3.5 3-5 6-5s6 1.5 6 5"/></svg>
      <svg width="18" height="14" viewBox="0 0 18 14" fill="none" stroke="#222" stroke-width="1.5"><rect x="1" y="1" width="16" height="12" rx="2"/><path d="M1 2l8 6 8-6"/></svg>
      <span>EN ⌄</span>
    </div>
  </div>
  <h1>THE SMART WAY TO<br>WORK INDEPENDENTLY.</h1>
  <p class="lead">We simplify payrolling so you can deliver your expertise with confidence.</p>
  <div class="btn" style="left:142px;top:424px;width:213px;height:41px">Discover Payrolling</div>
  <div class="clients"><span></span><span></span><span></span><div><b>500+</b><small>Corporate Clients</small></div></div>

  <svg class="abs" style="left:640px;top:180px" width="440" height="440"><circle cx="220" cy="220" r="210" fill="var(--pink)"/></svg>
  <div class="abs" role="img" aria-label="Smiling professional holding a laptop" style="left:705px;top:120px;width:300px;height:490px;border-radius:140px 140px 0 0;background:linear-gradient(180deg,#6a4b3c 0%,#3e3e42 40%,#2d2d30 100%)"></div>

  <div class="card" style="left:940px;top:145px;width:132px;height:108px;padding:10px">
    <b style="font-size:7px;color:#222">Payrolls</b>
    <div style="margin-top:8px;line-height:24px">● Nora Vell <span style="float:right">$2500</span><br>● Tom Brice <span style="float:right">$3500</span><br>● Ana Ruiz <span style="float:right">$2000</span></div>
  </div>
  <div class="card" style="left:593px;top:432px;width:232px;height:178px;padding:14px">
    <b style="font-size:10px;color:#222">Payroll Summary</b>
    <div style="margin-top:12px;display:flex;justify-content:space-between"><span>Current Week</span><span style="background:#4cd964;color:#fff;padding:0 6px;border-radius:3px">Week 1</span><span>Week 2</span><span>Week 3</span></div>
    <div style="margin-top:12px;display:flex;justify-content:space-between;line-height:11px">
      <span>Employee<br>Regular hours<br>Overtime hours<br>Regular pay total<br>Salary</span>
      <span>150<br>$600<br>$35<br>$4,700<br>$6,800</span>
      <span>Withholding<br>Social security<br>Medicare<br>Deductions</span>
      <span>150<br>$500<br>$35<br>$4,700</span>
    </div>
    <div style="margin-top:14px;display:flex;justify-content:space-between;align-items:center;color:#222"><b>Gross Wage</b><span>$10,800</span><b>Net Pay</b><span style="background:#3a7bec;color:#fff;padding:2px 8px;border-radius:3px">$6,200</span></div>
  </div>
</header>

<section class="services">
  <svg class="tick" style="top:60px" width="60" height="36" viewBox="0 0 60 36" fill="none" stroke="var(--pink)" stroke-width="5" stroke-linecap="round"><path d="M4 18l14 14L56 4"/></svg>
  <div class="h2">Discover All Our Services</div>
  <div class="svc" style="left:148px;top:205px">
    <svg class="ring" role="img" aria-label="Payrolling service icon" width="170" height="170"><circle cx="85" cy="85" r="84" fill="#fff"/><circle cx="85" cy="85" r="58" fill="#f7d3e6"/></svg>
    <h3>PAYROLLING</h3><p>Work with the best experts quickly, in<br>Switzerland and internationally.</p>
  </div>
  <div class="svc" style="left:468px;top:205px">
    <svg class="ring" role="img" aria-label="Sourcing service icon" width="170" height="170"><circle cx="85" cy="85" r="84" fill="var(--pink)"/><circle cx="85" cy="85" r="58" fill="#ef5ea5"/></svg>
    <h3>SOURCING</h3><p>Find the best talent to move your<br>business forward.</p>
  </div>
  <div class="svc" style="left:787px;top:212px">
    <svg class="ring" role="img" aria-label="Payroll outsourcing service icon" width="170" height="170"><circle cx="85" cy="85" r="84" fill="#fff"/><circle cx="85" cy="85" r="58" fill="#f7d3e6"/></svg>
    <h3>PAYROLL OUT SOURCE</h3><p>Outsource your employee payroll<br>management in full compliance.</p>
  </div>
</section>

<section class="partner">
  <svg class="tick" style="top:72px" width="60" height="36" viewBox="0 0 60 36" fill="none" stroke="var(--pink)" stroke-width="5" stroke-linecap="round"><path d="M4 18l14 14L56 4"/></svg>
  <div class="h2">Working with BRISK The Answer<br><span>Means working with a partner</span></div>
  <div class="features">
    <div class="feat" style="left:0"><div class="dia"></div><h4>Market leadership<br>&amp; reliability</h4><ul><li>Market leader in Swiss payrolling.</li><li>Proven financial stability and a solid infrastructure to support professionals and companies.</li></ul></div>
    <div class="feat" style="left:253px"><div class="dia"></div><h4>Our compliance &amp;<br>certification</h4><ul><li>Market leader in Swiss payrolling.</li><li>Proven financial stability and a solid infrastructure to support professionals and companies.</li></ul></div>
    <div class="feat" style="left:506px"><div class="dia pink"></div><h4>Agility &amp; responsiveness</h4><ul><li>Market leader in Swiss payrolling.</li><li>Proven financial stability and a solid infrastructure to support professionals and companies.</li></ul></div>
    <div class="feat" style="left:759px;border-right:0"><div class="dia"></div><h4>Digital first approach</h4><ul><li>Market leader in Swiss payrolling.</li><li>Proven financial stability and a solid infrastructure to support professionals and companies.</li></ul></div>
  </div>
</section>

<section class="solution">
  <div class="photo-right" role="img" aria-label="Smiling senior professional seated with a laptop in a bright office"></div>
  <svg class="abs" style="left:142px;top:92px" width="60" height="36" viewBox="0 0 60 36" fill="none" stroke="var(--pink)" stroke-width="5" stroke-linecap="round"><path d="M4 18l14 14L56 4"/></svg>
  <h2>BRISK Payroll <span>Solution</span></h2>
  <p style="top:220px">Lorem ipsum dolor sit amet, consectetur adipiscing elit, sed do eiusmod tempor incididunt ut labore et dolore magna aliqua. Ut enim ad minim veniam, quis nostrud exercitation ullamco laboris nisi ut aliquip ex ea commodo consequat. Duis aute irure dolor in reprehenderit in voluptate velit esse cillum dolore eu fugiat nulla pariatur. Excepteur sint occaecat cupidatat non proident, sunt in culpa qui officia deserunt mollit anim id est laborum.</p>
  <p style="top:416px">Lorem ipsum dolor sit amet, consectetur adipiscing elit, sed do eiusmod tempor incididunt ut labore et dolore magna aliqua. Ut enim ad minim veniam, quis nostrud</p>
  <div class="btn" style="left:143px;top:517px;width:214px;height:42px">Discover Payrolling</div>
</section>

<section class="why">
  <svg class="tick" style="top:88px" width="60" height="36" viewBox="0 0 60 36" fill="none" stroke="var(--pink)" stroke-width="5" stroke-linecap="round"><path d="M4 18l14 14L56 4"/></svg>
  <div class="h2">Why Choose <span style="font-weight:500">Us</span></div>
  <svg class="abs" style="left:150px;top:210px" width="900" height="320" fill="none" stroke="#555" stroke-width="2">
    <path d="M14 150 A145 145 0 0 1 290 90"/><circle cx="14" cy="150" r="5" fill="#555"/>
    <path d="M310 140 A145 145 0 0 0 590 140"/>
    <path d="M610 90 A145 145 0 0 1 886 150"/><circle cx="886" cy="150" r="5" fill="#555"/>
  </svg>
  <div class="bubble" style="left:175px;top:232px">
    <svg width="40" height="40" viewBox="0 0 40 40" fill="none" stroke="#fff" stroke-width="2"><path d="M14 36V16a3 3 0 016 0v8l10 2c3 1 3 3 2 6l-2 4"/><path d="M8 16a9 9 0 0118 0"/></svg>
    <h5>Management</h5><i></i><p>Sed ut perspiciatis unde omnis iste natus error sit voluptatem accu</p>
  </div>
  <div class="bubble pink" style="left:467px;top:232px">
    <svg width="40" height="40" viewBox="0 0 40 40" fill="none" stroke="#fff" stroke-width="2"><path d="M16 38V18a3 3 0 016 0v8l8 2c3 1 3 3 2 6l-2 4"/><path d="M20 4v6M10 8l3 4M30 8l-3 4"/></svg>
    <h5>Expertise</h5><i></i><p>Sed ut perspiciatis unde omnis iste natus error sit voluptatem accu</p>
  </div>
  <div class="bubble" style="left:759px;top:232px">
    <svg width="40" height="40" viewBox="0 0 40 40" fill="none" stroke="#fff" stroke-width="2"><path d="M12 36v-8c-4-3-6-7-5-12 1-7 8-11 15-10 8 1 12 9 9 16l3 5h-4v5h-7v4"/></svg>
    <h5>Accompaniement</h5><i></i><p>Sed ut perspiciatis unde omnis iste natus error sit voluptatem accusantium dolo</p>
  </div>
</section>

<section class="testimonials">
  <svg class="tick" style="top:76px" width="60" height="36" viewBox="0 0 60 36" fill="none" stroke="var(--pink)" stroke-width="5" stroke-linecap="round"><path d="M4 18l14 14L56 4"/></svg>
  <div class="h2">Our <span>Testimonials</span></div>
  <div class="avatar" role="img" aria-label="Client portrait"></div>
  <div class="arrow" style="left:63px"><svg width="12" height="16" fill="none" stroke="#222" stroke-width="2"><path d="M9 2L3 8l6 6"/></svg></div>
  <div class="arrow" style="left:1078px"><svg width="12" height="16" fill="none" stroke="#222" stroke-width="2"><path d="M3 2l6 6-6 6"/></svg></div>
  <p class="quote">Sed ut perspiciatis unde omnis iste natus error sit voluptatem accusantium doloremque laudantium, totam rem aperiam, eaque ipsa quae ab illo inventore veritatis et quasi architecto beatae vitae dicta sunt explicabo. Nemo enim ipsam voluptatem quia voluptas sit aspernatur aut odit aut fugit, sed quia consequuntur magni dolores eos qui ratione vo</p>
  <div class="who"><b>LIAM CARTER</b><span>Project Manager</span></div>
</section>

<section class="cta">
  <h2>Are you looking for a trusted partner<br>to support you in your need for freedom?</h2>
  <p>We simplify payrolling by handling contracts, payroll, and administration, giving you the flexibility to focus fully on your projects.</p>
  <div class="btn">Start Your Payrolling Journey</div>
</section>

<footer>
  <div class="logo">BRISK The Answer</div>
  <div class="social"><span></span><span></span><span></span></div>
  <div class="col" style="left:414px"><h6>Consultant</h6>How payrolling works<br>Our payrolling offer<br>Frequently Asked<br>Questions</div>
  <div class="col" style="left:662px"><h6>Business</h6>External talent management<br>Payroll Outsourcing<br>Talent sourcing<br>Are you an agency?</div>
  <div class="col" style="left:964px"><h6>About</h6>Who are we ?<br>Contact us</div>
  <div class="legal">Copyright@2025.All Rights Reserved</div>
</footer>

</body>
</html>
```